New Webpage for High Class Expert Witness Services Company

We are looking for a minimalist design for a webpage that just has our logo and an entry form offer to connect with one of our Liaisons.
The entry form should just ask for Name, Email, Contact Info and Description of Project.

Company Name is: The Marlowe Crest Advisory Services

Number of Pages Required

1 page

```html
<!DOCTYPE html>
<html lang="en">
<head>
<meta charset="utf-8">
<title>Marlowe Crest Advisory Services</title>
<link rel="stylesheet" href="https://fonts.googleapis.com/css2?family=Cinzel:wght@400;600&family=Manrope:wght@400&family=Roboto:wght@400&display=swap">
<style>
  :root {
    --bg-deep: #050505;
    --bg-mid: #141414;
    --text-light: #e6e6e6;
    --text-muted: #9a9a9a;
    --text-body: #c9c9c9;
    --panel-border: #6a6a6a;
    --field-border: #d0d0d0;
    --button-light: #e2e2e4;
    --button-dark: #a2a2a6;
    --button-text: #111111;
    --rule: #2e2e2e;
  }
  * { box-sizing: border-box; margin: 0; padding: 0; }
  html, body { width: 1200px; height: 743px; overflow: hidden; background: var(--bg-deep); }
  .page { position: relative; width: 1200px; height: 743px; overflow: hidden; background: var(--bg-deep); }
  .backdrop {
    position: absolute; inset: 0;
    background:
      radial-gradient(ellipse 260px 300px at 280px 300px, rgba(70,70,70,0.45), transparent 70%),
      radial-gradient(ellipse 420px 220px at 1020px 600px, rgba(60,60,60,0.35), transparent 70%),
      linear-gradient(160deg, var(--bg-mid) 0%, var(--bg-deep) 60%, #0a0a0a 100%);
  }
  .brand { position: absolute; left: 135px; top: 46px; display: flex; align-items: center; gap: 12px; }
  .brand-mark { width: 40px; height: 40px; background: var(--text-light); }
  .brand-name { font-family: "Cinzel", serif; font-weight: 400; color: var(--text-light); font-size: 26px; line-height: 1; letter-spacing: 1px; }
  .brand-name small { display: block; font-size: 13px; letter-spacing: 4px; margin-top: 6px; }
  .hero { position: absolute; left: 127px; top: 236px; width: 520px; }
  .hero-eyebrow { font-family: "Cinzel", serif; font-size: 19px; letter-spacing: 2.2px; color: var(--text-muted); }
  .hero-title { font-family: "Cinzel", serif; font-weight: 400; font-size: 49px; line-height: 54px; color: var(--text-light); margin-top: 16px; letter-spacing: 0.5px; }
  .hero-text { font-family: "Manrope", sans-serif; font-size: 15.5px; line-height: 28px; color: var(--text-body); margin-top: 16px; }
  .contact-panel {
    position: absolute; left: 719px; top: 122px; width: 380px; height: 440px;
    border: 1px solid var(--panel-border);
    background: radial-gradient(ellipse at 30% 20%, rgba(70,70,70,0.55), rgba(20,20,20,0.85) 75%);
    padding: 38px 45px 0;
  }
  .contact-title { font-family: "Cinzel", serif; font-weight: 400; font-size: 25px; color: var(--text-light); letter-spacing: 0.5px; margin-bottom: 19px; }
  .contact-form { display: flex; flex-direction: column; gap: 12px; }
  .field {
    width: 296px; height: 42px; border: 1px solid var(--field-border); background: transparent;
    font-family: "Roboto", sans-serif; font-size: 13px; color: var(--text-light); padding: 0 17px;
  }
  .field::placeholder { color: var(--text-light); }
  textarea.field { height: 89px; padding-top: 12px; resize: none; }
  .submit-button {
    width: 298px; height: 44px; border: none; margin-top: 1px;
    background: linear-gradient(110deg, var(--button-light) 55%, var(--button-dark) 80%);
    font-family: "Cinzel", serif; font-weight: 600; font-size: 16px; color: var(--button-text); letter-spacing: 0.5px;
  }
  .footer-rule { position: absolute; left: 0; top: 681px; width: 1200px; height: 1px; background: var(--rule); }
  .footer-text { position: absolute; left: 0; top: 701px; width: 1242px; text-align: center; font-family: "Roboto", sans-serif; font-size: 12.5px; color: var(--text-muted); }
</style>
</head>
<body>
<div class="page">
  <div class="backdrop" role="img" aria-label="Dark faceted stone texture with a faint mountain landscape"></div>

  <header class="brand">
    <span class="brand-mark"></span>
    <span class="brand-name">MARLOWE CREST<small>ADVISORY SERVICES</small></span>
  </header>

  <section class="hero">
    <p class="hero-eyebrow">MARLOWE CREST ADVISORY SERVICES</p>
    <h1 class="hero-title">SEAMLESS MEDICAL<br>EXPERT INTEGRATION</h1>
    <p class="hero-text">Lorem ipsum dolor sit amet, consectetur adipiscing elit, sed do eiusmod tempor incididunt ut labore et dolore magna aliqua.</p>
  </section>

  <section class="contact-panel">
    <h2 class="contact-title">CONNECT WITH US</h2>
    <form class="contact-form">
      <input class="field" type="text" placeholder="Name*">
      <input class="field" type="email" placeholder="Email*">
      <input class="field" type="tel" placeholder="Phone number*">
      <textarea class="field" placeholder="Description of Project"></textarea>
      <button class="submit-button" type="button">SUBMIT</button>
    </form>
  </section>

  <div class="footer-rule"></div>
  <p class="footer-text">© 2026 Marlowe Crest Advisory Services. All Rights Reserved</p>
</div>
</body>
</html>
```